Cover page and letterhead for athlete development program

We require an exciting and dynamic cover page with a second page letterhead in a word doc format for us to use as professional stationery for letter merges and portfolio documents. We are an athlete preparation company that specialises in training up and coming sports representatives in the fitness and sports science industry. We work with athletes from ages 13 - 24 mainly. If we could have images on the cover page from the sports of:
Rugby League
Rugby Union
Hockey
Cricket
AFL
Soccer
Track and Field
Netball
Basketball
Golf
Weight training

This would be a great start. Thank you

```html
<!DOCTYPE html>
<html lang="en">
<head>
<meta charset="utf-8">
<title>Rising Stride Letterhead</title>
<link href="https://fonts.googleapis.com/css2?family=Arimo:wght@400;700&display=swap" rel="stylesheet">
<style>
  :root {
    --backdrop: #d9dcdf;
    --paper: #ffffff;
    --ink: #111111;
    --body-grey: #8a8a8a;
    --contact-grey: #555555;
    --gold: #b4782f;
    --rule: #cfcfcf;
    --watermark: #f1f1f1;
  }
  * { box-sizing: border-box; margin: 0; padding: 0; }
  html, body { width: 1200px; height: 784px; overflow: hidden; }
  body {
    background: var(--backdrop);
    font-family: "Arimo", Arial, sans-serif;
    display: flex; align-items: center; justify-content: center;
  }
  .letterhead {
    position: relative;
    width: 524px; height: 740px;
    background: var(--paper);
    box-shadow: 0 6px 18px rgba(0,0,0,.15);
    overflow: hidden;
  }
  .side-band {
    position: absolute; left: 26px; top: 40px;
    width: 8px; height: 640px;
    background: linear-gradient(to bottom, rgba(0,0,0,0) 0%, #666 55%, var(--ink) 100%);
  }
  .gold-tab {
    position: absolute; left: 40px; top: 10px;
    width: 3px; height: 16px; background: var(--gold);
  }
  .gold-tab.second { left: 46px; }
  .brand {
    position: absolute; left: 48px; top: 38px;
    display: flex; align-items: center; gap: 10px;
  }
  .brand-square { width: 30px; height: 30px; background: var(--gold); flex: none; }
  .brand-name {
    font-weight: 700; font-size: 24px; line-height: 1.05;
    color: var(--ink); letter-spacing: 1px; text-transform: uppercase;
  }
  .contact {
    position: absolute; right: 30px; top: 100px;
    width: 176px; padding-left: 10px;
    border-left: 1px solid var(--rule);
    font-size: 7.5px; color: var(--contact-grey); line-height: 1.55;
    list-style: none;
  }
  .contact li { display: flex; align-items: flex-start; gap: 4px; }
  .contact .address { font-weight: 700; color: var(--ink); }
  .contact span { color: inherit; }
  .contact svg { width: 7px; height: 7px; margin-top: 2px; flex: none; }
  .letter-body {
    position: absolute; left: 58px; top: 190px; width: 330px;
    font-size: 9.5px; line-height: 1.45; color: var(--body-grey);
  }
  .letter-body p { margin-bottom: 12px; text-indent: 18px; }
  .letter-body p:first-child { text-indent: 0; }
  .signature {
    position: absolute; left: 58px; top: 610px;
    width: 150px; height: 36px;
    background: linear-gradient(90deg, rgba(150,150,150,.2), rgba(150,150,150,0));
  }
  .corner-shade {
    position: absolute; left: 40px; top: 655px;
    width: 120px; height: 85px; background: var(--watermark);
  }
</style>
</head>
<body>
  <main class="letterhead">
    <div class="side-band"></div>
    <div class="gold-tab"></div>
    <div class="gold-tab second"></div>

    <header class="brand">
      <span class="brand-square"></span>
      <span class="brand-name">Rising<br>Stride</span>
    </header>

    <ul class="contact">
      <li class="address">
        <svg viewBox="0 0 10 10"><circle cx="5" cy="5" r="5" fill="#333"/><circle cx="5" cy="4" r="1.6" fill="#fff"/></svg>
        <span>1200 Harbor Way, Ste 100, Coral Bay, US&nbsp;00010</span>
      </li>
      <li>
        <svg viewBox="0 0 10 10"><circle cx="5" cy="5" r="5" fill="#333"/><rect x="3.5" y="2.5" width="3" height="5" rx=".6" fill="#fff"/></svg>
        <span>000-000-0100 &nbsp; 000-000-0120</span>
      </li>
      <li>
        <svg viewBox="0 0 10 10"><circle cx="5" cy="5" r="5" fill="#333"/><rect x="2.5" y="3.2" width="5" height="3.6" fill="#fff"/></svg>
        <span>hello@risingstride.example</span>
      </li>
      <li>
        <svg viewBox="0 0 10 10"><circle cx="5" cy="5" r="5" fill="#333"/><circle cx="5" cy="5" r="2.4" fill="none" stroke="#fff" stroke-width=".8"/></svg>
        <span>www.risingstride.example</span>
      </li>
    </ul>

    <section class="letter-body">
      <p>Lorem Ipsum is simply dummy text of the printing and typesetting industry. Lorem Ipsum has been the industry's standard dummy text ever since the 1500s, when an unknown printer took a galley of type and scrambled it to make a type specimen book. It has survived not only five centuries, but also the leap into electronic typesetting, remaining essentially unchanged. It was popularised in the 1960s with the release of TypeSheet sheets containing Lorem Ipsum passages, and more recently with desktop publishing software like PageForge Studio including versions of Lorem Ipsum.</p>
      <p>It is a long established fact that a reader will be distracted by the readable content of a page when looking at its layout. The point of using Lorem Ipsum is that it has a more-or-less normal distribution of letters, as opposed to using 'Content here, content here', making it look like readable English. Many desktop publishing packages and web page editors now use Lorem Ipsum as their default model text, and a search for 'lorem ipsum' will uncover many web sites still in their infancy. Various versions have evolved over the years, sometimes by accident, sometimes on purpose (injected humour and the like).</p>
      <p>Contrary to popular belief, Lorem Ipsum is not simply random text. It has roots in a piece of classical Latin literature from 45 BC, making it over 2000 years old. Dana Whitfield, a Latin professor at Northgate College in Maplewood, looked up one of the more obscure Latin words, consectetur, from a Lorem Ipsum passage, and going through the cites of the word in classical literature, discovered the undoubtable source. Lorem Ipsum comes from sections 1.10.32 and 1.10.33 of "de Rebus Variis et Minoribus" structures, to generate Lorem Ipsum which looks reasonable. The generated Lorem Ipsum is therefore always free from repetition, injected humour, or non-characteristic words etc.</p>
    </section>

    <div class="signature" role="img" aria-label="Handwritten signature"></div>
    <div class="corner-shade"></div>
  </main>
</body>
</html>
```